Residential building / Apartments for sale landing page

I need a website / landing page design for my latest development project - a residential building with 70+ apartments for sale. I need the design in layers in Photoshop/Illustrator/InDesign format with all the icons/shapes/maps/graphic assets in vector format (svg, ai, eps) as much as possible.

I prefer white website and please consider the performance/coding experience. We're not making something suitable only for a design contest with fancy parallax effects and confusing animations. We're trying to create usable and clean UI with good UX.

The website will be custom coded, i.e. I'm not using WordPress.

I know that the existing 3D photos are not good but for now you can use them or replace them with some stock photos. I'm going to create new 3D photos soon.

Real Estate Development

1 page

```html
<!DOCTYPE html>
<html lang="en">
<head>
<meta charset="utf-8">
<title>Verdant Heights – Apartments for Sale</title>
<link href="https://fonts.googleapis.com/css2?family=Poppins:wght@300;400;500;600;700&display=swap" rel="stylesheet">
<style>
:root{
  --green:#8cc63f;
  --green-dark:#6fa52b;
  --ink:#231f20;
  --text:#333;
  --muted:#666;
  --line:#e6e6e6;
  --dark:#282425;
  --footer:#f4f5f7;
}
*{margin:0;padding:0;box-sizing:border-box}
html,body{width:1200px;height:5305px;overflow:hidden}
body{position:relative;font-family:'Poppins',sans-serif;color:var(--text);background:#fff}
.abs{position:absolute}
a{color:inherit;text-decoration:none}

/* nav */
.nav{left:0;top:0;width:1200px;height:92px;background:#fff}
.brand{left:88px;top:26px;display:flex;align-items:center;gap:8px;font-weight:700;font-size:20px;color:var(--ink);letter-spacing:.5px}
.brand .mark{width:14px;height:14px;background:var(--green)}
.menu{left:393px;top:36px;display:flex;gap:26px;font-size:11px;font-weight:500;color:var(--ink);text-transform:uppercase}
.menu .cta{background:#f1f1f1;padding:8px 18px;margin-top:-8px}
.lang{left:1048px;top:36px;font-size:11px;display:flex;gap:6px;align-items:center}
.lang i{width:14px;height:14px;border-radius:50%;background:#c9d3e6;display:inline-block}

/* hero */
.hero{left:0;top:92px;width:1200px;height:623px;background:linear-gradient(90deg,#f7f7f7,#e4e4e4)}
.hero-green{left:755px;top:92px;width:445px;height:310px;background:var(--green)}
.hero-img{left:690px;top:150px;width:510px;height:565px;background:linear-gradient(160deg,#e9eee4,#9fbf7a 55%,#5d7c3c);}
.hero h1{left:88px;top:248px;font-size:46px;font-weight:400;line-height:56px;color:var(--ink)}
.hero h1 b{color:var(--green);font-weight:600}
.price{left:88px;top:430px;font-size:20px;color:var(--ink)}
.btn-dark{left:88px;top:490px;width:150px;height:48px;background:var(--ink);color:#fff;font-size:12px;font-weight:600;display:flex;align-items:center;justify-content:center;gap:10px}

/* headings */
.h2{width:1200px;left:0;text-align:center;font-size:46px;font-weight:400;color:var(--ink)}
.h2 b{font-weight:600}
.h2.light{color:#fff}
.rule{left:576px;width:48px;height:3px;background:var(--green)}
.sub{width:1200px;left:0;text-align:center;font-size:14px;color:var(--muted)}

/* project */
.proj-img{left:88px;top:770px;width:487px;height:530px;background:linear-gradient(135deg,#5d7f2e,#a7c474 50%,#d9d9d9);box-shadow:0 20px 40px rgba(0,0,0,.15)}
.proj-title{left:667px;top:970px;font-size:46px;line-height:54px;color:var(--ink)}
.proj-title b{font-weight:600}
.proj-rule{left:623px;top:1100px;width:92px;height:3px;background:var(--green)}
.proj-text{left:670px;top:1122px;width:440px;font-size:14px;line-height:27px;color:var(--muted)}

/* cards */
.card{width:329px;height:486px;top:1542px;background:#fff;box-shadow:0 6px 24px rgba(0,0,0,.08)}
.card .img{height:218px;background:linear-gradient(160deg,#dfe8d6,#8fae64 60%,#55703a)}
.card .tag{position:absolute;left:22px;top:34px;font-size:11px;color:#fff;font-weight:600}
.card .price{position:absolute;right:0;top:196px;background:var(--green);color:#fff;font-weight:600;font-size:19px;padding:10px 18px}
.card .status{position:absolute;left:24px;top:252px;background:#eee;font-size:10px;font-weight:600;padding:3px 10px;color:var(--ink)}
.card h3{position:absolute;left:24px;top:284px;font-size:18px;font-weight:500;color:var(--ink)}
.card p{position:absolute;left:24px;top:322px;width:280px;font-size:12px;line-height:20px;color:var(--muted)}
.card .meta{position:absolute;left:24px;top:392px;display:flex;gap:22px;font-size:11px;color:var(--muted)}
.card .meta span::before{content:"";display:inline-block;width:14px;height:10px;border:1.5px solid #888;margin-right:5px;vertical-align:-1px}
.card .view{position:absolute;left:24px;top:428px;font-size:22px;font-weight:600;color:var(--ink);border-bottom:3px solid #ddd;padding-right:24px;line-height:26px}
.arrow{width:26px;height:26px;background:#f1f1f1;display:flex;align-items:center;justify-content:center;font-size:12px;color:#555}

/* facilities */
.fac{top:2342px;width:242px;height:298px;background:#fff;box-shadow:0 6px 24px rgba(0,0,0,.08);z-index:2}
.fac svg{position:absolute;left:26px;top:40px}
.fac h4{position:absolute;left:26px;top:126px;font-size:18px;font-weight:500;color:var(--ink)}
.fac p{position:absolute;left:26px;top:162px;width:200px;font-size:12px;line-height:22px;color:var(--muted)}
.fac .go{position:absolute;left:26px;top:246px;color:#999;font-size:16px}
.fac.active{background:var(--green)}
.fac.active h4,.fac.active p,.fac.active .go{color:#fff}

.dark{left:0;top:2603px;width:1200px;height:692px;background:var(--dark)}
.feat{width:440px;color:#fff}
.feat .n{position:absolute;left:-28px;top:-2px;font-size:20px;font-weight:700;color:#4a4546}
.feat h5{font-size:15px;font-weight:600}
.feat p{font-size:12px;line-height:21px;color:#bdb8b9;margin-top:6px}

/* location */
.loc{left:88px;top:3545px;width:1022px;height:500px;background:#fff;box-shadow:0 6px 30px rgba(0,0,0,.1)}
.loc ul{list-style:none;position:absolute;left:26px;top:36px;width:200px}
.loc li{height:71px;border-bottom:1px solid var(--line);display:flex;justify-content:space-between;align-items:center;font-size:14px;color:var(--ink)}
.map{left:249px;top:0;width:773px;height:500px;background:linear-gradient(135deg,#eef0f2,#dfe3e8)}

.gal{top:4268px;width:255px;height:357px;background:linear-gradient(170deg,#cfdbe4,#86a768 55%,#4b6535)}
.gal span{position:absolute;left:34px;bottom:28px;color:#fff;font-size:13px}
.gal b{position:absolute;right:50px;bottom:22px;color:var(--green);font-size:24px;font-weight:600}

/* footer */
.footer{left:0;top:4710px;width:1200px;height:595px;background:var(--footer)}
.foot-brand{left:88px;top:4835px;font-size:30px;font-weight:700;color:var(--ink);display:flex;align-items:center;gap:10px}
.foot-brand i{width:18px;height:18px;background:var(--green)}
.foot-text{left:88px;top:4908px;width:300px;font-size:13px;line-height:22px;color:var(--muted)}
.ci{left:88px;width:300px;font-size:12px;line-height:18px;color:var(--muted);padding-left:24px}
.ci b{color:var(--ink);font-weight:600;display:block}
.ci svg{position:absolute;left:0;top:2px}
.social{top:5125px;width:24px;height:24px;border-radius:50%}
.cf-title{left:545px;top:4820px;font-size:44px;color:var(--ink)}
.cf-title b{font-weight:600}
.lbl{font-size:12px;font-weight:500;color:var(--ink)}
.field{background:#fff;border:1px solid #ebebeb;height:42px;font-size:12px;color:#999;padding:12px 16px}
.submit{left:545px;top:5140px;width:126px;height:42px;background:var(--green);color:#fff;font-size:13px;font-weight:600;display:flex;align-items:center;justify-content:center}
.foot-line{left:88px;top:5240px;width:1022px;height:1px;background:#ddd}
.copy{left:0;top:5266px;width:1200px;text-align:center;font-size:13px;color:var(--ink)}
.top{left:1133px;top:5198px;width:44px;height:44px;border-radius:50%;background:var(--green);color:#fff;display:flex;align-items:center;justify-content:center}
</style>
</head>
<body>

<header class="abs nav">
  <div class="abs brand"><span class="mark"></span>VERDANT HEIGHTS</div>
  <nav class="abs menu">
    <a>Verdant Heights</a><a>The Project</a><a>Apartments/Sales</a><a>Location</a><a>Gallery</a><a class="cta">Contact</a>
  </nav>
  <div class="abs lang"><i></i>ENG ▾</div>
</header>

<section>
  <div class="abs hero"></div>
  <div class="abs hero-green"></div>
  <div class="abs hero-img" role="img" aria-label="3D rendering of the residential building with green terraces"></div>
  <h1 class="abs" style="left:88px;top:248px;font-size:46px;font-weight:400;line-height:56px;color:var(--ink)">Sale Of Apartments<br>Directly From The investor<br>with <b style="color:var(--green);font-weight:600">10% discount</b></h1>
  <div class="abs price">Price from XXX EUR/m2</div>
  <a class="abs btn-dark">BUY NOW <svg width="16" height="10" viewBox="0 0 16 10"><path d="M0 5h14M10 1l4 4-4 4" stroke="#fff" stroke-width="1.5" fill="none"/></svg></a>
</section>

<section>
  <div class="abs proj-img" role="img" aria-label="Aerial rendering of the building complex"></div>
  <h2 class="abs proj-title">Project<br><b>Presentation</b></h2>
  <div class="abs proj-rule"></div>
  <p class="abs proj-text">Architecture, building materials – facades, roof, common areas etc.), information board (assignor, contractor, etc.), maintenance and management info, level of completion, etc.</p>
</section>

<section>
  <h2 class="abs h2" style="top:1400px">Apartments/<b>Sales</b></h2>
  <div class="abs rule" style="top:1473px"></div>
  <p class="abs sub" style="top:1493px">Table with all apartments (70) – unit, floor, entrance/block, typology (1 bed, 2 beds, etc)</p>
  <div class="abs arrow" style="left:30px;top:1773px">‹</div>
  <div class="abs arrow" style="left:1142px;top:1773px">›</div>

  <article class="abs card" style="left:88px">
    <div class="img" role="img" aria-label="Building rendering, one bed apartment"></div>
    <span class="tag">SALE</span><span class="price">$320 000</span>
    <span class="status">Available</span>
    <h3>One bed apartment</h3>
    <p>Aenean sollicitudin, lorem quis bibendum auctor nisi elit consequat ipsum...</p>
    <div class="meta"><span>2450 sq</span><span>06</span><span>05</span><span>Yes</span></div>
    <a class="view">View</a>
  </article>
  <article class="abs card" style="left:434px">
    <div class="img" role="img" aria-label="Aerial building rendering, two bed apartment"></div>
    <span class="tag">SALE</span><span class="price">$320 000</span>
    <span class="status">Available</span>
    <h3>Two bed apartment</h3>
    <p>Aenean sollicitudin, lorem quis bibendum auctor nisi elit consequat ipsum...</p>
    <div class="meta"><span>2450 sq</span><span>06</span><span>05</span><span>Yes</span></div>
    <a class="view">View</a>
  </article>
  <article class="abs card" style="left:780px">
    <div class="img" role="img" aria-label="Building rendering with hills, three bed apartment"></div>
    <span class="tag">SALE</span><span class="price">$320 000</span>
    <span class="status">Available</span>
    <h3>Three bed apartment</h3>
    <p>Aenean sollicitudin, lorem quis bibendum auctor nisi elit consequat ipsum...</p>
    <div class="meta"><span>2450 sq</span><span>06</span><span>05</span><span>Yes</span></div>
    <a class="view">View</a>
  </article>
</section>

<p class="abs sub" style="top:2120px;font-size:17px;color:var(--ink)">Map / Layout of the project with:</p>

<section>
  <div class="abs dark"></div>
  <h2 class="abs h2" style="top:2188px">Facilities/<b>Benefits</b></h2>
  <div class="abs rule" style="top:2261px"></div>
  <p class="abs sub" style="top:2280px">Etiam rhoncus maecenas tempus tellus eget condim entum rhon cus sem quam semper</p>
  <div class="abs arrow" style="left:30px;top:2460px">‹</div>
  <div class="abs arrow" style="left:1142px;top:2460px">›</div>

  <div class="abs fac" style="left:88px">
    <svg width="64" height="60" viewBox="0 0 64 60" fill="none" stroke="#333" stroke-width="2"><rect x="4" y="4" width="56" height="52" rx="4"/><rect x="14" y="24" width="36" height="16" rx="3"/><path d="M18 24l4-10h20l4 10"/><circle cx="20" cy="44" r="3"/><circle cx="44" cy="44" r="3"/></svg>
    <h4>Parking spaces</h4><p>Etiam rhoncus maecenas cus tempus tellus ui condim entum rhon cus...</p><span class="go">→</span>
  </div>
  <div class="abs fac" style="left:350px">
    <svg width="70" height="60" viewBox="0 0 70 60" fill="none" stroke="#333" stroke-width="2"><path d="M30 6v36M44 6v36M30 18h14M30 30h14"/><path d="M4 46c6-5 10 5 16 0s10 5 16 0 10 5 16 0 10 5 14 0M4 54c6-5 10 5 16 0s10 5 16 0 10 5 16 0 10 5 14 0"/></svg>
    <h4>Pool</h4><p>Etiam rhoncus maecenas cus tempus tellus ui condim entum rhon cus...</p><span class="go">→</span>
  </div>
  <div class="abs fac" style="left:610px">
    <svg width="70" height="60" viewBox="0 0 70 60" fill="none" stroke="#333" stroke-width="2"><rect x="4" y="2" width="22" height="22"/><path d="M11 18V8h5a4 4 0 010 8h-5"/><circle cx="20" cy="46" r="10"/><circle cx="54" cy="46" r="10"/><path d="M20 46l10-14h16l8 14M30 32l8 14h-18M38 26h8"/></svg>
    <h4>Bicycle parking</h4><p>Etiam rhoncus maecenas cus tempus tellus ui condim entum rhon cus...</p><span class="go">→</span>
  </div>
  <div class="abs fac active" style="left:869px">
    <svg width="70" height="60" viewBox="0 0 70 60" fill="none" stroke="#fff" stroke-width="2"><path d="M10 34a22 22 0 0144 0zM6 38h52M32 8v4"/><circle cx="32" cy="6" r="3"/><path d="M4 50h14l10 4h20l12-8"/></svg>
    <h4>Restaurant</h4><p>Etiam rhoncus maecenas cus tempus tellus ui condim entum rhon cus...</p><span class="go">→</span>
  </div>
</section>

<section>
  <h2 class="abs h2 light" style="top:2725px">Construction/<b>Features</b></h2>
  <div class="abs rule" style="top:2797px"></div>
  <p class="abs sub" style="top:2813px;color:#d0cccd">Etiam rhoncus maecenas tempus tellus eget condim entum rhon cus sem quam semper</p>

  <div class="abs feat" style="left:178px;top:2880px"><span class="n">1</span><h5>Norvex Windows</h5><p>5 chamber noise reducing glazing with high temperature and noise insulation efficiency</p></div>
  <div class="abs feat" style="left:178px;top:2970px"><span class="n">2</span><h5>Calderstone bricks</h5><p>Regional Calderstone ThermaCore bricks with porous system and 25 cm thick outer walls</p></div>
  <div class="abs feat" style="left:178px;top:3060px"><span class="n">3</span><h5>High Ceilings</h5><p>2.70m high ceilings giving the light and space you need</p></div>
  <div class="abs feat" style="left:178px;top:3150px"><span class="n">4</span><h5>Thermal Insulation</h5><p>System Mureno – Mureno Silicone Plaster Thermal insulation system 10 cm thick and 15 cm thick from the north walls</p></div>
  <div class="abs feat" style="left:638px;top:2880px"><span class="n">5</span><h5>Air conditioners</h5><p>All air conditioners piping systems are installed – ready to plug in the inside and outside body of the aircon system</p></div>
  <div class="abs feat" style="left:638px;top:2970px"><span class="n">6</span><h5>HPL ventilated facade</h5><p>Facadeline GmbH – Suspended ventilated facade with highly pressed laminated panels by Facadeline GmbH in wood color</p></div>
  <div class="abs feat" style="left:638px;top:3060px"><span class="n">7</span><h5>Panoramic Altavia lifts</h5><p>Overlooking the park – Giving you the everyday glimpse over the inside garden and putting a smile on your face</p></div>
  <div class="abs feat" style="left:638px;top:3150px"><span class="n">8</span><h5>Waterproofing with PVC</h5><p>Membrane Tegmar – PVC membrane with high puncture and tear resistance, UV resistance and vapor permeability</p></div>
</section>

<section>
  <h2 class="abs h2" style="top:3383px">Our<b>Location</b></h2>
  <div class="abs rule" style="top:3456px"></div>
  <p class="abs sub" style="top:3472px;left:230px;width:740px;line-height:22px">Neighborhood, local attractions, metro/bus stops, schools nearby, big shops etc.Maybe some sort of infographic with distance to the POI above.</p>
  <div class="abs loc">
    <ul>
      <li>Neighborhood<span>›</span></li><li>Local attractions<span>›</span></li><li>Landmarks<span>›</span></li><li>Metro/bus stops<span>›</span></li><li>Schools nearby<span>›</span></li><li>Big shops<span>›</span></li>
    </ul>
    <div class="abs map" role="img" aria-label="Street map of the neighborhood with points of interest and the building location at 14 Linden Row, Maple Park"></div>
  </div>
</section>

<section>
  <h2 class="abs h2" style="top:4128px">Our/<b>Gallery</b></h2>
  <div class="abs rule" style="top:4200px"></div>
  <p class="abs sub" style="top:4220px">Boxes for each month with photos of the construction progress</p>
  <div class="abs gal" style="left:205px" role="img" aria-label="Rendering of the finished building"><span>April 2021</span><b>View</b></div>
  <div class="abs gal" style="left:472px;background:linear-gradient(170deg,#d8c8a8,#a38a5e 55%,#6f5a3a)" role="img" aria-label="Building under construction with scaffolding"><span>April 2021</span><b>View</b></div>
  <div class="abs gal" style="left:739px" role="img" aria-label="Rendering of the building with mountains"><span>April 2021</span><b>View</b></div>
</section>

<footer>
  <div class="abs footer"></div>
  <div class="abs foot-brand"><i></i>VERDANT HEIGHTS</div>
  <p class="abs foot-text">Please select a topic below related to your inquiry. If you don't find what you need, fill out our contact form</p>
  <div class="abs ci" style="top:4980px"><svg width="14" height="16" viewBox="0 0 14 16"><path d="M7 1a5 5 0 015 5c0 4-5 9-5 9S2 10 2 6a5 5 0 015-5z" fill="var(--green)"/></svg><b>Location*</b>Some address goes here city name country name</div>
  <div class="abs ci" style="top:5040px"><svg width="14" height="14" viewBox="0 0 14 14"><path d="M3 1l3 3-2 2a8 8 0 004 4l2-2 3 3-2 2C6 13 1 8 1 3z" fill="var(--green)"/></svg><b>Phone*</b>Call Us +00 555 010 2040</div>
  <div class="abs ci" style="top:5090px"><svg width="14" height="12" viewBox="0 0 14 12"><rect x="0" y="1" width="14" height="10" fill="var(--green)"/><path d="M0 1l7 5 7-5" stroke="#fff" fill="none"/></svg><b>Email*</b>hello@verdantheights.test</div>
  <span class="abs social" style="left:90px;background:#3b5998"></span>
  <span class="abs social" style="left:122px;background:#1da1f2"></span>

  <h2 class="abs cf-title">Contact <b>Form</b></h2>
  <label class="abs lbl" style="left:545px;top:4916px">Name*</label>
  <label class="abs lbl" style="left:737px;top:4916px">Email*</label>
  <label class="abs lbl" style="left:928px;top:4916px">Phone*</label>
  <div class="abs field" style="left:545px;top:4938px;width:182px">Enter your name</div>
  <div class="abs field" style="left:737px;top:4938px;width:182px">Enter your email</div>
  <div class="abs field" style="left:928px;top:4938px;width:182px">Enter your phone</div>
  <label class="abs lbl" style="left:545px;top:4992px">Message*</label>
  <div class="abs field" style="left:545px;top:5014px;width:565px;height:110px">Type your text</div>
  <a class="abs submit">SUBMIT</a>
  <a class="abs top">↑</a>
  <div class="abs foot-line"></div>
  <p class="abs copy">© Copyright 2021 Verdant Heights All Rights Reserved</p>
</footer>

</body>
</html>
```